Computer consultant business card

Bexil Software is a newly started computer consulting company. It's a small one-man company that provides mostly Vornix applications but also websites in collaboration with designers. I'm running this company on the side of full time university studies.

I want the final design to be clean and memorable. Be creative! :)

Some inspiration:
http://www.pixelmarta.com/design/48317
http://www.pixelmarta.com/design/2739164/business-card-design-by-frostlynk
http://www.pixelmarta.com/design/604281/business-card-design-by-koralind-vestrabanu

See attachment for my company logo.
Updates

I would like to thank everyone for submitting! I'll need a couple of days to review and ultimately select a design.

Target Market(s)

Non-technical entrepreneurs and small companies.

Industry/Entity Type

University

Requirements
Must have
• My company logo.
In any way, both colors from my logo.
First- and last name, e-mail and phone number.
Double-sided design.
Nice to have
• Something creative with the symbol in my logo

```html
<!DOCTYPE html>
<html lang="en">
<head>
<meta charset="utf-8">
<title>Business Card Set</title>
<link rel="stylesheet" href="https://fonts.googleapis.com/css2?family=Questrial&family=Jost:wght@400;600&family=Source+Sans+3:wght@400&display=swap">
<style>
  :root {
    --backdrop: #a3845c;
    --label: #1e1a16;
    --card-black: #000000;
    --card-white: #ffffff;
    --brand-blue: #4a74c0;
    --brand-dark: #333333;
    --text-light: #ffffff;
    --text-muted: #cfcfcf;
    --rule: #4a4a4a;
    --slate-deep: #2a2b31;
    --slate-blue: #4b5b86;
  }
  * { margin: 0; padding: 0; box-sizing: border-box; }
  html, body { width: 1200px; height: 788px; overflow: hidden; }
  body { background: var(--backdrop); font-family: "Source Sans 3", sans-serif; }
  .sheet { position: relative; width: 1200px; height: 788px; }

  .side-label {
    position: absolute; width: 524px; text-align: center;
    font-size: 21px; color: var(--label); font-family: "Source Sans 3", sans-serif;
  }
  .card {
    position: absolute; width: 524px; height: 300px; border-radius: 20px;
    overflow: hidden; box-shadow: 0 2px 6px rgba(0,0,0,.35);
  }
  .card--front { left: 54px; top: 74px; background: var(--card-black); }
  .card--white { left: 622px; top: 74px; background: var(--card-white); }
  .card--dots  { left: 54px; top: 445px; background: var(--card-black); }
  .card--slate { left: 622px; top: 445px;
    background: radial-gradient(ellipse 90% 110% at 80% 100%, var(--slate-blue) 0%, #3a4160 45%, var(--slate-deep) 100%); }

  .brand { position: absolute; display: flex; align-items: center; font-family: "Questrial", sans-serif; }
  .brand__dot { border-radius: 50%; background: var(--brand-blue); flex: none; }
  .brand__name { line-height: 1; }

  .card--front .brand { left: 34px; top: 42px; gap: 20px; }
  .card--front .brand__dot { width: 74px; height: 74px; }
  .card--front .brand__name { font-size: 62px; color: var(--text-light); }

  .holder { position: absolute; right: 31px; top: 206px; text-align: right; color: var(--text-light);
    font-family: "Jost", sans-serif; }
  .holder__name { font-size: 18px; font-weight: 600; line-height: 1.2; }
  .holder__role { font-size: 12px; color: var(--text-muted); margin-top: 1px; }
  .divider { position: absolute; left: 32px; right: 31px; top: 252px; height: 1px; background: var(--rule); }
  .contact { position: absolute; top: 259px; display: flex; align-items: center; gap: 8px;
    font-family: "Jost", sans-serif; font-size: 15px; color: var(--text-light); }
  .contact--phone { left: 33px; }
  .contact--mail { right: 31px; }
  .contact svg { width: 11px; height: 11px; fill: var(--text-light); }

  .card--white .brand { left: 105px; top: 92px; gap: 25px; }
  .card--white .brand__dot, .card--dots .brand__dot, .card--slate .brand__dot { width: 104px; height: 104px; }
  .card--white .brand__name { font-size: 86px; color: var(--brand-dark); }
  .card--dots .brand { left: 106px; top: 102px; gap: 25px; }
  .card--dots .brand__name, .card--slate .brand__name { font-size: 86px; color: var(--text-light); }
  .card--slate .brand { left: 98px; top: 106px; gap: 25px; }

  .web { position: absolute; left: 0; right: 0; text-align: center;
    font-family: "Questrial", sans-serif; font-size: 18px; letter-spacing: 3.6px; }
  .card--white .web { top: 250px; color: var(--brand-dark); }
  .card--dots .web { top: 256px; color: var(--text-light); }
  .card--slate .web { top: 256px; color: var(--text-light); }

  .texture { position: absolute; }
  .texture--top { left: 0; top: -60px; width: 340px; height: 200px;
    background: radial-gradient(closest-side, rgba(120,120,120,.5), rgba(0,0,0,0)); }
  .texture--bottom { left: 290px; top: 150px; width: 280px; height: 200px;
    background: radial-gradient(closest-side, rgba(140,130,140,.5), rgba(0,0,0,0)); }
</style>
</head>
<body>
<main class="sheet">
  <div class="side-label" style="left:54px; top:33px;">Front</div>
  <div class="side-label" style="left:622px; top:33px;">Back - 1</div>
  <div class="side-label" style="left:54px; top:403px;">Back - 2</div>
  <div class="side-label" style="left:622px; top:403px;">Back - 3</div>

  <section class="card card--front">
    <div class="brand"><span class="brand__dot"></span><span class="brand__name">qelvo</span></div>
    <div class="holder">
      <div class="holder__name">First Name + Last Name</div>
      <div class="holder__role">Designation</div>
    </div>
    <div class="divider"></div>
    <div class="contact contact--phone">
      <svg viewBox="0 0 12 12"><path d="M2.5 1l2 2.2-1 1.2a6 6 0 0 0 3.9 3.9l1.2-1 2.2 2-1.2 1.6C5 11 1 7 .9 2.2z"/></svg>
      <span>+12 345 6789</span>
    </div>
    <div class="contact contact--mail">
      <svg viewBox="0 0 12 12"><path d="M1 3h10v7H1z"/></svg>
      <span>info@qelvo-apps.com</span>
    </div>
  </section>

  <section class="card card--white">
    <div class="brand"><span class="brand__dot"></span><span class="brand__name">qelvo</span></div>
    <div class="web">www.qelvo-apps.com</div>
  </section>

  <section class="card card--dots">
    <div class="texture texture--top" role="img" aria-label="Perforated metal dot texture"></div>
    <div class="texture texture--bottom" role="img" aria-label="Perforated metal dot texture"></div>
    <div class="brand"><span class="brand__dot"></span><span class="brand__name">qelvo</span></div>
    <div class="web">www.qelvo-apps.com</div>
  </section>

  <section class="card card--slate">
    <div class="brand"><span class="brand__dot"></span><span class="brand__name">qelvo</span></div>
    <div class="web">www.qelvo-apps.com</div>
  </section>
</main>
</body>
</html>
```